Oil Field Service company needs professional business cards

Looking to clean up our current company business cards and look a little more professional. Brenwick Casing Services is a US based company that services the oil field. We deal with engineers, managers and oil rigs....................................................................................................................................................................................................................................................................................................................................................................................................

Target Market(s)

Oil and Gas professionals

Industry/Entity Type

Oil And Gas

Contact Information for Business Card

See attached photo as example

Font styles to use
Sans Serif

Colors
ec1f27

Requirements
Must have
• Company Logo, Name, Title, Cell, Office, Fax, Email.
• See attached photo
Nice to have
• External CRT, Internal CRT, Casing Crews, Torque Turn, Laydown Machine
Should not have
• Do not introduce any new pictures and keep it professional looking

```html
<!DOCTYPE html>
<html lang="en">
<head>
<meta charset="utf-8">
<title>Brenwick Casing Services – Business Card</title>
<link rel="stylesheet" href="https://fonts.googleapis.com/css2?family=Open+Sans:ital,wght@0,400;0,600;1,400&display=swap">
<style>
  :root {
    --brand-red: #ec1f27;
    --brand-red-light: #f2464d;
    --ink: #3d4651;
    --ink-soft: #5b6470;
    --paper: #ffffff;
    --backdrop: #e9e6e1;
  }
  * { box-sizing: border-box; margin: 0; padding: 0; }
  html, body {
    width: 1200px; height: 950px; overflow: hidden;
    background: var(--backdrop);
    font-family: "Open Sans", Arial, sans-serif;
  }
  .canvas {
    width: 1200px; height: 950px;
    display: flex; align-items: center; justify-content: center; gap: 40px;
  }
  .card {
    position: relative;
    width: 540px; height: 309px;
    overflow: hidden;
    box-shadow: 0 6px 18px rgba(0,0,0,.18);
  }

  /* Company name placeholder */
  .company {
    display: flex; align-items: center; gap: 10px;
    font-weight: 600; font-size: 22px; line-height: 1;
    white-space: nowrap;
  }
  .company-mark { width: 14px; height: 14px; flex: none; }

  /* Front */
  .card--front { background: var(--paper); }
  .front-band {
    position: absolute; left: 0; right: 0; top: 62px; height: 40px;
    background: var(--brand-red);
  }
  .front-band::after {
    content: ""; position: absolute; left: 0; right: 0; top: 0; height: 14px;
    background: var(--brand-red-light);
  }
  .card--front .company {
    position: absolute; left: 34px; top: 134px;
    color: var(--ink);
  }
  .card--front .company-mark { background: var(--brand-red); }

  .person { position: absolute; left: 60px; top: 196px; }
  .person-name { font-size: 20px; font-weight: 400; color: var(--brand-red); }
  .person-title { font-size: 12.5px; color: var(--ink-soft); margin-top: 4px; padding-left: 52px; }
  .person-address { font-size: 12.5px; color: var(--ink-soft); margin-top: 3px; padding-left: 40px; }

  .contacts {
    position: absolute; left: 345px; top: 180px;
    list-style: none; font-size: 12px; color: var(--ink-soft);
  }
  .contacts li { display: flex; align-items: center; gap: 8px; height: 19px; }
  .contacts svg { width: 11px; height: 11px; fill: var(--brand-red); flex: none; }

  /* Back */
  .card--back {
    background: var(--brand-red);
    color: var(--paper);
    display: flex; flex-direction: column; align-items: center; justify-content: center;
  }
  .card--back .company { color: var(--paper); font-size: 26px; }
  .card--back .company-mark { background: var(--paper); }
  .services {
    margin-top: 34px; text-align: center; font-style: italic; font-size: 13px; line-height: 1.55;
  }
</style>
</head>
<body>
<main class="canvas">

  <section class="card card--front" aria-label="Business card front">
    <div class="front-band"></div>
    <div class="company">
      <span class="company-mark" aria-hidden="true"></span>
      Brenwick Casing Services
    </div>

    <div class="person">
      <div class="person-name">Cody Hartwell</div>
      <div class="person-title">Area Manager</div>
      <div class="person-address">Ridgeton, OK 73000</div>
    </div>

    <ul class="contacts">
      <li>
        <svg viewBox="0 0 12 12" aria-hidden="true"><path d="M2.5 1l2 2.2-1 1.3a6 6 0 0 0 4 4l1.3-1 2.2 2-1.3 1.5C5.3 11 1 6.7 1 2.3z"/></svg>
        (555)210-4400
      </li>
      <li>
        <svg viewBox="0 0 12 12" aria-hidden="true"><path d="M3 0h6v12H3zM4 1.5v8h4v-8z" fill-rule="evenodd"/></svg>
        (555)318-2261
      </li>
      <li>
        <svg viewBox="0 0 12 12" aria-hidden="true"><path d="M3 0h6v3H3zM1 4h10v6H9v2H3v-2H1zM4 8v3h4V8z" fill-rule="evenodd"/></svg>
        (555)210-4410
      </li>
      <li>
        <svg viewBox="0 0 12 12" aria-hidden="true"><path d="M0 2h12v8H0zM1 3l5 3.5L11 3z" fill-rule="evenodd"/></svg>
        cody@brenwick.com
      </li>
      <li>
        <svg viewBox="0 0 12 12" aria-hidden="true"><circle cx="6" cy="6" r="6"/></svg>
        www.brenwick.com
      </li>
    </ul>
  </section>

  <section class="card card--back" aria-label="Business card back">
    <div class="company">
      <span class="company-mark" aria-hidden="true"></span>
      Brenwick Casing Services
    </div>
    <p class="services">
      External CRT | Internal CRT | Casing Crews<br>
      Torque Turn | Laydown Machine
    </p>
  </section>

</main>
</body>
</html>
```